QVR business card

Need a business card for a company that provides instructional design and elearning development services. The website is here: http://quorvane.studio/

I'm attaching a current logo, as well as the old business card design. While I like to keep it clean, the old design is too simplistic for my liking. The only idea I want to reuse from the old design is placing industry jargon on the back of the card, just need a better way to present it. But if you have other ideas for the back--feel free to experiment.

Please use the colors complementary to the color we have on the website. Thank you!

```html
<!DOCTYPE html>
<html lang="en">
<head>
<meta charset="utf-8">
<title>QVR business card</title>
<link rel="stylesheet" href="https://fonts.googleapis.com/css2?family=Open+Sans:wght@400;600;700&display=swap">
<style>
  :root {
    --backdrop: #3b3533;
    --card-black: #0d0d0d;
    --teal: #33b5ae;
    --teal-text: #2fb7b0;
    --white: #ffffff;
    --white-soft: rgba(255,255,255,0.92);
    --sand: #d9cf98;
  }
  * { margin: 0; padding: 0; box-sizing: border-box; }
  html, body {
    width: 1200px; height: 900px; overflow: hidden;
    background: var(--backdrop);
    font-family: "Open Sans", Arial, sans-serif;
  }
  .stage {
    position: relative; width: 1200px; height: 900px;
    display: flex; align-items: center; justify-content: center; gap: 50px;
  }
  .card {
    width: 500px; height: 286px; position: relative;
    box-shadow: 0 10px 24px rgba(0,0,0,0.45);
  }
  .card-front {
    background: var(--card-black);
    display: flex; flex-direction: column; align-items: center;
    padding-top: 58px;
  }
  .brand { display: flex; align-items: center; gap: 12px; }
  .brand-mark { width: 26px; height: 26px; background: var(--teal); }
  .brand-name {
    font-size: 46px; font-weight: 700; color: var(--sand);
    letter-spacing: 2px; line-height: 1;
  }
  .holder-name {
    margin-top: 34px; font-size: 17px; font-weight: 600;
    color: var(--teal-text); letter-spacing: 0.3px;
  }
  .contact-list { list-style: none; margin-top: 10px; text-align: center; }
  .contact-item {
    display: flex; align-items: center; justify-content: center; gap: 7px;
    font-size: 13.5px; color: var(--white-soft); line-height: 21px;
  }
  .contact-icon { width: 11px; height: 11px; fill: var(--teal-text); }
  .card-back {
    background: var(--teal);
    padding: 104px 0 0 52px; color: var(--white);
  }
  .help-title { font-size: 20px; font-weight: 700; letter-spacing: 0.3px; }
  .service-list { list-style: none; margin-top: 6px; padding-left: 22px; }
  .service-item { font-size: 15px; line-height: 19px; color: var(--white-soft); }
</style>
</head>
<body>
<main class="stage">
  <section class="card card-front">
    <div class="brand">
      <span class="brand-mark"></span>
      <span class="brand-name">QVR</span>
    </div>
    <p class="holder-name">Marin Kestrel</p>
    <ul class="contact-list">
      <li class="contact-item">
        <svg class="contact-icon" viewBox="0 0 24 24"><path d="M6.6 10.8a15.1 15.1 0 0 0 6.6 6.6l2.2-2.2a1 1 0 0 1 1-.25 11.4 11.4 0 0 0 3.6.57 1 1 0 0 1 1 1V20a1 1 0 0 1-1 1A17 17 0 0 1 3 4a1 1 0 0 1 1-1h3.5a1 1 0 0 1 1 1c0 1.25.2 2.45.57 3.57a1 1 0 0 1-.25 1z"/></svg>
        555-013-2847
      </li>
      <li class="contact-item">
        <svg class="contact-icon" viewBox="0 0 24 24"><path d="M2 5h20v14H2z M2 5l10 8 10-8" /></svg>
        mkestrel@quorvane.studio
      </li>
      <li class="contact-item">
        <svg class="contact-icon" viewBox="0 0 24 24"><circle cx="12" cy="12" r="10"/></svg>
        www.quorvane.studio
      </li>
    </ul>
  </section>

  <section class="card card-back">
    <h2 class="help-title">HOW CAN WE HELP?</h2>
    <ul class="service-list">
      <li class="service-item">Mobile Learning Scorm</li>
      <li class="service-item">Instructional Design Lms</li>
      <li class="service-item">Moocs Elearning Html5</li>
      <li class="service-item">Adult Learning Theory</li>
      <li class="service-item">Gamification Classroom</li>
      <li class="service-item">Xapi Blended Learning</li>
    </ul>
  </section>
</main>
</body>
</html>
```